Cloud Hosting Startup, and Panthers!

Hi!

We are quillvoxhub.example

A new hosting service that aims to provide awesome hosting and a bit of development work for free to get people set up.

We have decided on a logo and a theme. Awesome Panthers.

So, we are all about Panthers =)

-

We greatly desire a super super cool vector scene for the homepage. We love mountains, blue mountains, and green grass. Panthers hiding in long grass or leaping through the air to accentuate the coolness of our service would also be most appreciated.

Panthers hiding amongst crisp blue mountains, or hanging out on snowy mountain peaks thinking Panther things.

Or in green grassy jungles, hiding next to rocks and scaring zebras.

Or something =)

-

For the sub pages we would just like a style guide, showing the standard h1,h2's and some other items for layout.

As you can see at quillvoxhub.example we are almost ready for launch, we are web developers ourselves, and so we got the site design as far as we could.

We have our software written and ready for customers, however the site just doesn't tell you what its about from a glance! That's why we need you. So, Panthers, Cool cool, sweet Panthers to accentuate our cool new launch and hosting service.

We have included the vectors used and the site design as it stands. We would like to remain with the three items 'mini-panther', 'standard panther', and 'epic panther' from this page: quillvoxhub.example/signup

Apart from the epic panthers, and some variation of the panthers used for the logo, we are not fully attached other elements. We have gone with a strong red white and black, but we are just wacky developers, we need your help!

Looking forward to some great designs! If you are inspired by Panthers and super cool web hosting, this project is for you.

Thanks!!

The Quillvoxhub.example Team
Updates

Project payment has been guaranteed, we are committed to a result

Just a quick update based on a designer question:

We have spent many weeks of drinking coffee and coding, we have finished all the coding, all done!

If you take a look at Quillvoxhub.example you can see the result.

Basically we are looking for someone to take what we have already done (files attached of all our work) and make it less like a developer designed it, which is what happened along the way =)

Help us zarn vel quistomar ..
 

Basically, we are looking for increased awesome.

We have a really cool, cheap hosting and template product offering, we would love it if someone could breathe the life of Panther into it =)

Ok,

Thanks =)

Sorry, one more update =)

Basically we are not looking for an entire site re-design, the major thing is a cool scene for the homepage with panthers and mountains =)

We are just looking for a touch up, a polish, someone to give it the design magic that communicates the message in the copy we have written. We have worked out our product and completed it, we just need someone to help us bring it to the market.

Ok, thanks!

One final update then we will return to coding our Panther and leave you all alone =)

Our internet heroes are: http://www.zintaly.example/

We love them, their purple colour scheme makes us unhappy, but we so love their signup and plan selection process.

Ok!

Thanks so much, from Quillvoxhub Team

Reason: Deadline has been extended one day to allow new designers time to prepare some panther concepts. We will also use the extra day to await funds transfer to increase the budget of the project and hopefully add a 2nd place prize (lunaforge fees permitting) Thanks everyone! Torvald Quillvoxhub.example

Thanks all!

Reason: Deadline extended a further one day, 1st prize and 2nd prize payments have been updated today, looking forward to submissions! Thanks everyone

Just an update, really great designs coming in, loving all the panther concepts =)

We will award the competition on the 21st, and we have two prizes now, we will award one based on visual design and appeal (the most stunning panther), and one based on use of copy and user interface (the easiest panther)

Ok!

Thanks, hope you have enjoyed designing, we have definitely enjoyed receiving designs to bring our idea to life

Thanks!!

Torvald

Quillvoxhub

Sorry!

One more update, we have added a third prize now of $100 

We love the designs too much not to make use of them =)

Ok!

Last update =)

Thanks all

Hi All,

Wonderful work, thanks everyone for feedback and revisions

We have only one day of the competition left, we are asking now for final submissions, we have provided a style guide template here:

http://quillvoxhub.example/web_final_template.psd

The team will judge the competition tomorrow, we have now 3 prizes and we will add 2 participation payments as a fourth prize as we have asked some designers for some strange requests =)

Ok!

Looking forward to final submissions with the home page and style guide, thanks again!

Torvald

Quillvoxhub

Target Market(s)

Tech savvy people, but not tech geniuses, young fun people who at least know what web-hosting is

Industry/Entity Type

Software

Requirements
Must have
• - super super cool vector landscape for the homepage
- some number of sub pages, in accordance with the site structure as it stands

```html
<!DOCTYPE html>
<html lang="en">
<head>
<meta charset="utf-8">
<title>Quillvoxhub Style Guide</title>
<link rel="stylesheet" href="https://fonts.googleapis.com/css2?family=Noto+Sans:wght@400;700&family=Noto+Serif:ital,wght@0,700;1,400&family=PT+Sans:wght@400;700&display=swap">
<style>
  :root {
    --page-bg: #e0dbd3;
    --logo-bg: #0b090a;
    --logo-text: #f2b233;
    --heading: #24200f;
    --subheading: #4a3f22;
    --quote-bg: #ece8e0;
    --quote-text: #666360;
    --quote-mark: #8a8580;
    --accent-blue: #1c6a8a;
    --bullet: #b07510;
    --bullet-text: #555049;
  }
  * { box-sizing: border-box; margin: 0; padding: 0; }
  html, body { width: 1200px; height: 900px; overflow: hidden; }
  body {
    position: relative;
    background: var(--page-bg);
    font-family: "Noto Sans", sans-serif;
    color: var(--heading);
  }
  .backdrop { position: absolute; inset: 0; background: var(--page-bg); }

  .brand {
    position: absolute; left: 130px; top: 0; width: 220px; height: 96px;
    background: var(--logo-bg);
    display: flex; align-items: center; justify-content: center; gap: 10px;
  }
  .brand-dot { width: 46px; height: 46px; border-radius: 50%; background: #f4f2ee; }
  .brand-name {
    font-family: "Noto Sans", sans-serif; font-weight: 700; font-size: 14px;
    color: var(--logo-text); letter-spacing: -0.2px;
  }

  .mega-heading {
    position: absolute; left: 126px; top: 262px;
    font-size: 51px; font-weight: 400; line-height: 1.2;
  }
  .section-heading {
    position: absolute; left: 127px; top: 350px;
    font-size: 33px; font-weight: 400; line-height: 1.2;
  }
  .subheading {
    position: absolute; left: 129px; top: 405px;
    font-size: 24px; font-weight: 400; line-height: 1.2; color: var(--subheading);
  }

  .testimonial {
    position: absolute; left: 130px; top: 456px; width: 586px; height: 144px;
    background: var(--quote-bg);
  }
  .quote-mark {
    position: absolute; left: 21px; top: 10px;
    font-family: "Noto Serif", serif; font-weight: 700; font-size: 34px; color: var(--quote-mark);
  }
  .quote-body {
    position: absolute; left: 47px; top: 32px; width: 490px;
    font-family: "PT Sans", sans-serif; font-size: 15.5px; line-height: 22px; color: var(--quote-text);
  }
  .quote-author {
    position: absolute; right: 15px; top: 102px;
    font-family: "PT Sans", sans-serif; font-size: 11.5px; color: var(--accent-blue);
  }
  .quote-author strong { text-transform: uppercase; }

  .direction-nav {
    position: absolute; left: 148px; top: 608px;
    display: flex; align-items: center; gap: 10px;
    font-family: "Noto Serif", serif; font-weight: 700; font-size: 9.5px;
    text-transform: uppercase; color: var(--accent-blue); letter-spacing: 0.2px;
  }

  .list-heading {
    position: absolute; left: 129px; top: 676px;
    font-size: 22px; font-weight: 400; line-height: 1.2;
  }
  .dotpoints { position: absolute; left: 131px; top: 732px; list-style: none; }
  .dotpoints li {
    display: flex; align-items: center; gap: 9px; height: 24px; margin-bottom: 14px;
    font-family: "Noto Serif", serif; font-style: italic; font-size: 16.5px; color: var(--bullet-text);
  }
  .dotpoints li:last-child { margin-top: 2px; }
  .bullet-dot { width: 22px; height: 22px; border-radius: 50%; background: var(--bullet); flex: none; }
</style>
</head>
<body>
  <div class="backdrop" role="img" aria-label="Fine zigzag pattern in warm light grey"></div>

  <header class="brand">
    <span class="brand-dot"></span>
    <span class="brand-name">Brackenfold Sites</span>
  </header>

  <h1 class="mega-heading">Heading: Mega Heading</h1>
  <h2 class="section-heading">Heading: This is a heading</h2>
  <h3 class="subheading">Subheading</h3>

  <blockquote class="testimonial">
    <span class="quote-mark">&ldquo;</span>
    <p class="quote-body">Over the last eighteen months our sales have increased four thousand percent since the launch of our new web site. We have to say it<br>has made us delighted we chose Quillvoxhub.</p>
    <p class="quote-author"><strong>Marlo Penwright,</strong> Finance Minister</p>
  </blockquote>

  <nav class="direction-nav">
    <svg width="8" height="12" viewBox="0 0 8 12" aria-hidden="true"><path d="M6.5 1.5 2 6l4.5 4.5" fill="none" stroke="#1c6a8a" stroke-width="2.4"/></svg>
    <span>Some arrows for direction</span>
    <svg width="8" height="12" viewBox="0 0 8 12" aria-hidden="true"><path d="M1.5 1.5 6 6l-4.5 4.5" fill="none" stroke="#1c6a8a" stroke-width="2.4"/></svg>
  </nav>

  <h4 class="list-heading">Some dotpoints</h4>
  <ul class="dotpoints">
    <li><span class="bullet-dot"></span>Point one, and some text</li>
    <li><span class="bullet-dot"></span>Point two</li>
    <li><span class="bullet-dot"></span>Point 3, and some more text.</li>
  </ul>
</body>
</html>
```